Landing Page & Email Signature

I am looking for a new landing page as well as an email signature to align with the change in business. I have included the new logo/emblem which I'd like incorporated into the design and the current landing page is www.delmorquivex.com.au should you wish to see the old version.

```html
<!DOCTYPE html>
<html lang="en">
<head>
<meta charset="utf-8">
<title>Delmor Transport &amp; Logistics</title>
<link href="https://fonts.googleapis.com/css2?family=Montserrat:wght@400;500;600;700&display=swap" rel="stylesheet">
<style>
  :root {
    --bg-dark: #1f1d1c;
    --bg-mid: #3a3530;
    --bg-warm: #4a3d31;
    --text: #ffffff;
    --text-soft: #e9e6e3;
    --brand-red: #c8202e;
    --field-fill: rgba(255, 255, 255, 0.22);
    --field-line: rgba(255, 255, 255, 0.85);
  }
  * { box-sizing: border-box; margin: 0; padding: 0; }
  html, body { width: 1200px; height: 667px; overflow: hidden; }
  body {
    position: relative;
    font-family: "Montserrat", sans-serif;
    color: var(--text);
    background: var(--bg-dark);
  }
  .hero-photo {
    position: absolute; inset: 0;
    background:
      radial-gradient(ellipse at 30% 60%, rgba(70, 74, 80, 0.55), transparent 55%),
      radial-gradient(ellipse at 62% 55%, rgba(110, 82, 56, 0.5), transparent 50%),
      linear-gradient(135deg, var(--bg-mid) 0%, var(--bg-dark) 45%, var(--bg-warm) 75%, var(--bg-dark) 100%);
  }
  .site-header {
    position: absolute; left: 90px; right: 89px; top: 36px;
    display: flex; justify-content: space-between; align-items: flex-start;
  }
  .brand { display: flex; flex-direction: column; gap: 4px; }
  .brand-name {
    font-weight: 700; font-size: 22px; letter-spacing: 0.5px; color: var(--text);
    display: flex; align-items: center; gap: 8px;
  }
  .brand-mark { width: 14px; height: 14px; background: var(--brand-red); }
  .brand-url { font-size: 8px; font-weight: 600; color: var(--brand-red); padding-left: 22px; }
  .menu-toggle {
    display: flex; align-items: center; gap: 8px; margin-top: 24px;
    font-size: 19px; font-weight: 400; letter-spacing: 0.5px; color: var(--text);
  }
  .intro { position: absolute; left: 90px; top: 215px; width: 540px; }
  .intro-title { font-size: 50px; font-weight: 600; letter-spacing: -1px; line-height: 1; }
  .intro-text { margin-top: 37px; font-size: 13.2px; line-height: 20.6px; color: var(--text-soft); }
  .contact { margin-top: 19px; font-size: 13.2px; line-height: 20.6px; color: var(--text-soft); padding-left: 1px; }
  .enquiry-form {
    position: absolute; left: 681px; top: 167px; width: 430px;
    display: flex; flex-direction: column; gap: 13px;
  }
  .field {
    height: 36px; background: var(--field-fill); border: 1px solid var(--field-line);
    padding: 0 17px; display: flex; align-items: center;
    font-size: 18px; color: var(--text); letter-spacing: 0.3px;
  }
  .field-message { height: 126px; align-items: flex-start; padding-top: 7px; }
  .submit-button {
    margin-top: 17px; width: 183px; height: 36px;
    background: var(--brand-red); border: 1px solid var(--field-line);
    display: flex; align-items: center; justify-content: center;
    font-size: 19px; font-weight: 600; letter-spacing: 0.4px; color: var(--text);
  }
  .site-footer {
    position: absolute; left: 0; right: 0; top: 627px;
    text-align: center; font-size: 13px; color: var(--text-soft);
  }
</style>
</head>
<body>
  <div class="hero-photo" role="img" aria-label="Dimmed photo of two warehouse workers in caps checking parcels beside shelves of cardboard boxes"></div>

  <header class="site-header">
    <div class="brand">
      <div class="brand-name"><span class="brand-mark"></span>DELMOR TRANSPORT</div>
      <div class="brand-url">www.delmorquivex.com.au</div>
    </div>
    <div class="menu-toggle">MENU
      <svg width="22" height="14" viewBox="0 0 22 14"><g stroke="#fff" stroke-width="2"><line x1="0" y1="1" x2="22" y2="1"/><line x1="0" y1="7" x2="22" y2="7"/><line x1="0" y1="13" x2="22" y2="13"/></g></svg>
    </div>
  </header>

  <section class="intro">
    <h1 class="intro-title">QUALIITY IS PRIORITY</h1>
    <p class="intro-text">We can guarantee your satisfaction with our services. To prove, you may call our clients, who we have been serving for years to hear&nbsp; first-hand testimonies.<br>We look forward to satisfy your current and future needs!</p>
    <p class="contact">Phone : +61412558307<br>Email : delmortransport@mailbox.com</p>
  </section>

  <form class="enquiry-form">
    <div class="field">Enter Your Name</div>
    <div class="field">Enter Your Phone Number</div>
    <div class="field">Enter Your Email Adress</div>
    <div class="field field-message">Enter Message</div>
    <div class="submit-button">ENQUIRE NOW</div>
  </form>

  <footer class="site-footer">© Copyright 2020 Delmor Transport &amp; Logistics | All Rights Reserved. Designed by Brightgrid Studio.</footer>
</body>
</html>
```